Interior Design/ decoration business card design

This card is for my Interior Design and Decoration business and later I will also be selling homewares. I would like the card to be very simple in design and like either white, duck egg blue , aquas or metallics on a flat mat card excellent quality card. It needs to be well designed as that is my field. I dont like fuss, the simpler the better. I would like a styalised brim under the name brim if possible. SIMPLE, STYLISH, CLASSIC, TASTEFUL

Target Market(s)

40 + year olds who are building or rennovating.

Industry/Entity Type

Business

Contact Information for Business Card

Brim
styling, design, homeware

Marnie Callow
p 0427163958
e marnie@brimhouse.com.au
w brimhouse.com.au

Requirements
Must have
• very simple, stylish, classic, sophisticated. Simple and easy to read text that is a print similar to attached image. I like simple round A's though not as in attached image.

Double sided. It wont save as double sided for some reason!!
Should not have
• not too much colour, No animated / cartoon pictures.

```html
<!DOCTYPE html>
<html lang="en">
<head>
<meta charset="utf-8">
<title>Brim business card</title>
<link rel="stylesheet" href="https://fonts.googleapis.com/css2?family=Exo+2:wght@300;400&family=Oswald:wght@500&display=swap">
<style>
  :root{
    --backdrop:#dfe3e2;
    --duck-egg:#cfe4df;
    --aqua-deep:#6f9e98;
    --paper:#ffffff;
    --ink:#2f3d3b;
    --ink-soft:#4f6562;
  }
  *{box-sizing:border-box;margin:0;padding:0}
  html,body{width:1200px;height:863px;overflow:hidden;background:var(--backdrop)}
  .canvas{width:1200px;height:863px;display:flex;flex-direction:column;align-items:center;justify-content:center;gap:40px}
  .card{position:relative;width:660px;height:377px;overflow:hidden;font-family:"Exo 2",sans-serif;box-shadow:0 2px 10px rgba(47,61,59,.12)}

  /* reverse side */
  .card--reverse{background:var(--duck-egg)}
  .reverse-band{position:absolute;left:78px;top:70px;width:504px;height:180px;background:var(--paper);display:flex;align-items:center;justify-content:center}
  .wordmark{font-family:"Exo 2",sans-serif;font-weight:300;color:var(--ink);font-size:66px;letter-spacing:1px;line-height:1}
  .reverse-web{position:absolute;left:0;right:0;top:282px;text-align:center;color:var(--ink-soft);font-size:15px;letter-spacing:1px}

  /* front side */
  .card--front{background:var(--paper)}
  .front-panel{position:absolute;left:300px;top:0;width:360px;height:377px;background:var(--duck-egg)}
  .front-logo{position:absolute;left:0;top:0;width:300px;height:377px;display:flex;align-items:center;justify-content:center;padding-top:40px}
  .name-tab{position:absolute;left:0;top:0}
  .name-block{position:absolute;left:332px;top:58px;color:var(--paper)}
  .person-name{font-family:"Oswald",sans-serif;font-weight:500;font-size:32px;letter-spacing:1px;line-height:1}
  .person-role{font-size:12px;letter-spacing:1.5px;margin-top:6px;text-transform:uppercase}
  .contact-list{position:absolute;left:336px;top:165px;list-style:none;color:var(--ink)}
  .contact-row{display:flex;align-items:center;gap:16px;height:56px}
  .contact-icon{width:34px;height:34px;flex:none}
  .contact-text{font-size:14px;line-height:1.25;letter-spacing:.5px}
</style>
</head>
<body>
<main class="canvas">

  <section class="card card--reverse" aria-label="Card reverse">
    <div class="reverse-band"><span class="wordmark">brim</span></div>
    <p class="reverse-web">www.brimhouse.com.au</p>
  </section>

  <section class="card card--front" aria-label="Card front">
    <div class="front-panel"></div>
    <div class="front-logo"><span class="wordmark">brim</span></div>
    <svg class="name-tab" width="660" height="377" viewBox="0 0 660 377" aria-hidden="true">
      <polygon points="288,46 660,46 660,128 300,128 300,112 288,100" fill="var(--aqua-deep)"/>
    </svg>
    <div class="name-block">
      <h1 class="person-name">MARNIE CALLOW</h1>
      <p class="person-role">General Manager</p>
    </div>
    <ul class="contact-list">
      <li class="contact-row">
        <svg class="contact-icon" viewBox="0 0 34 34" aria-hidden="true">
          <circle cx="17" cy="17" r="17" fill="var(--paper)"/>
          <path d="M17 8a6 6 0 0 0-6 6c0 5 6 12 6 12s6-7 6-12a6 6 0 0 0-6-6z" fill="var(--aqua-deep)"/>
          <circle cx="17" cy="14" r="2.2" fill="var(--paper)"/>
        </svg>
        <span class="contact-text">12 Wren Lane Road,<br>2nd floor Hollis St.</span>
      </li>
      <li class="contact-row">
        <svg class="contact-icon" viewBox="0 0 34 34" aria-hidden="true">
          <circle cx="17" cy="17" r="17" fill="var(--paper)"/>
          <path d="M9 14c0-3 4-5 8-5s8 2 8 5l-3 1-1-3h-8l-1 3z" fill="var(--aqua-deep)"/>
          <rect x="11" y="16" width="12" height="8" rx="2" fill="var(--aqua-deep)"/>
          <circle cx="17" cy="20" r="2" fill="var(--paper)"/>
        </svg>
        <span class="contact-text">0427 163 958</span>
      </li>
      <li class="contact-row">
        <svg class="contact-icon" viewBox="0 0 34 34" aria-hidden="true">
          <circle cx="17" cy="17" r="17" fill="var(--paper)"/>
          <g fill="none" stroke="var(--aqua-deep)" stroke-width="1.6">
            <circle cx="17" cy="17" r="8"/>
            <ellipse cx="17" cy="17" rx="3.5" ry="8"/>
            <line x1="9" y1="17" x2="25" y2="17"/>
            <line x1="10.5" y1="12.5" x2="23.5" y2="12.5"/>
            <line x1="10.5" y1="21.5" x2="23.5" y2="21.5"/>
          </g>
        </svg>
        <span class="contact-text">marnie@brimhouse.com.au<br>www.brimhouse.com.au</span>
      </li>
    </ul>
  </section>

</main>
</body>
</html>
```